Heron Loan Partners Business Card

We need a business card design for our mortgage servicing company. In addition to servicing the loans of homeowners, we help homeowners with purchasing their homes and any mortgage refinancing. We would like to see designs that use the colors in the logo attached below (gold-ish yellow and navy blue), and any other design you deem fit! The design should communicate a simpler life with smart mortgages provided by Heron.

```html
<!DOCTYPE html>
<html lang="en">
<head>
<meta charset="utf-8">
<title>Heron Loan Partners Business Card</title>
<link rel="stylesheet" href="https://fonts.googleapis.com/css2?family=Abhaya+Libre:wght@400;700;800&display=swap">
<style>
  :root {
    --backdrop: #b3b3b3;
    --gold: #dfb13f;
    --navy: #27215a;
    --paper: #ffffff;
    --ink: #1c1a2a;
  }
  * { margin: 0; padding: 0; box-sizing: border-box; }
  html, body { width: 1154px; height: 1200px; overflow: hidden; }
  body {
    background: var(--backdrop);
    position: relative;
    font-family: "Abhaya Libre", Georgia, serif;
  }
  .card {
    position: absolute;
    left: 190px;
    width: 773px;
    height: 441px;
    border-radius: 32px;
    box-shadow: 0 8px 10px rgba(0, 0, 0, 0.16);
  }
  .card--front { top: 138px; background: var(--gold); }
  .card--back { top: 620px; background: var(--paper); }

  .brand-name {
    position: absolute;
    left: 0;
    width: 100%;
    text-align: center;
    font-weight: 800;
    font-size: 54px;
    letter-spacing: 0.5px;
    color: var(--navy);
    line-height: 1;
  }
  .card--front .brand-name { top: 192px; }
  .card--back .brand-name { top: 115px; }

  .holder {
    position: absolute;
    right: 394px;
    top: 272px;
    text-align: right;
  }
  .holder__name {
    font-weight: 700;
    font-size: 30px;
    color: var(--navy);
    letter-spacing: 0.3px;
    line-height: 1;
  }
  .holder__role {
    margin-top: 10px;
    font-size: 18px;
    color: var(--ink);
    letter-spacing: 0.8px;
    line-height: 1;
  }
  .divider {
    position: absolute;
    left: 409px;
    top: 255px;
    width: 1.5px;
    height: 86px;
    background: var(--navy);
  }
  .contacts {
    position: absolute;
    left: 428px;
    top: 254px;
    list-style: none;
  }
  .contacts li {
    display: flex;
    align-items: center;
    height: 30px;
    font-size: 19px;
    color: var(--ink);
    letter-spacing: 0.4px;
  }
  .contacts svg { width: 18px; height: 18px; margin-right: 13px; flex: none; }
  .address {
    position: absolute;
    left: 0;
    width: 100%;
    top: 382px;
    text-align: center;
    font-size: 19px;
    color: var(--ink);
    letter-spacing: 0.3px;
  }
</style>
</head>
<body>
  <section class="card card--front">
    <p class="brand-name">Heron Loan Partners</p>
  </section>

  <section class="card card--back">
    <p class="brand-name">Heron Loan Partners</p>

    <div class="holder">
      <p class="holder__name">DANIEL HARPER</p>
      <p class="holder__role">MANAGING DIRECTOR</p>
    </div>

    <div class="divider"></div>

    <ul class="contacts">
      <li>
        <svg viewBox="0 0 24 24" aria-hidden="true"><path fill="var(--gold)" d="M6.6 10.8a15.2 15.2 0 0 0 6.6 6.6l2.2-2.2c.3-.3.7-.4 1-.2 1.1.4 2.3.6 3.6.6.6 0 1 .4 1 1V20c0 .6-.4 1-1 1C10.6 21 3 13.4 3 4c0-.6.4-1 1-1h3.5c.6 0 1 .4 1 1 0 1.3.2 2.5.6 3.6.1.3 0 .7-.2 1z"/></svg>
        044-210 987 654
      </li>
      <li>
        <svg viewBox="0 0 24 24" aria-hidden="true"><rect x="2" y="5" width="20" height="14" fill="var(--gold)"/><path d="M2 5l10 8 10-8M2 19l7-6M22 19l-7-6" fill="none" stroke="#fff" stroke-width="1.5"/></svg>
        hello@heronloans.com
      </li>
      <li>
        <svg viewBox="0 0 24 24" aria-hidden="true"><g fill="none" stroke="var(--gold)" stroke-width="2"><circle cx="12" cy="12" r="9.5"/><ellipse cx="12" cy="12" rx="4" ry="9.5"/><path d="M2.5 12h19M4 7h16M4 17h16"/></g></svg>
        www.heronloans.com
      </li>
    </ul>

    <p class="address">18, Harbour Street Suite 4&nbsp; 20731, Eastland</p>
  </section>
</body>
</html>
```